Marlo clean Business Cards

I'm looking for someone to design my business card using my company name and logo. I would like it it be clean, fresh and a little out of the box. The colors I would like used are the same two in my logo (gold and the teal blue color) I also want it to screen high end scene the company name is Marlo clean :) I'm a commercial cleaning company based out of Orange and San Diego county. Once I receive your email I will send over the file. Because the file is quote big with several options of logos. Please be an out of the box thinker and take some risk...I'm looking for someone to put themselves out there. Thanks and good luck

```html
<!DOCTYPE html>
<html lang="en">
<head>
<meta charset="utf-8">
<title>Marlo clean Business Cards</title>
<link rel="stylesheet" href="https://fonts.googleapis.com/css2?family=Michroma&family=Exo+2:wght@400;500&display=swap">
<style>
  :root {
    --backdrop: #e6e7e9;
    --card: #f4f5f6;
    --brand-teal: #1d8c98;
    --brand-gold: #c9a24a;
    --gold-light: #e6c878;
    --ink: #2e3135;
    --muted: #b9bcc0;
    --white: #ffffff;
  }
  * { margin: 0; padding: 0; box-sizing: border-box; }
  html, body {
    width: 1200px; height: 1085px; overflow: hidden;
    background: var(--backdrop);
  }
  .card {
    position: absolute; left: 180px;
    width: 840px; height: 480px;
    background: var(--card);
    border-radius: 4px;
    box-shadow: 0 14px 30px rgba(0,0,0,0.14);
    overflow: hidden;
  }
  .card--front { top: 40px; }
  .card--back { top: 565px; }

  /* Front */
  .brand {
    position: absolute; left: 0; right: 0; top: 150px;
    display: flex; align-items: center; justify-content: center; gap: 26px;
  }
  .brand__mark {
    width: 70px; height: 70px; border-radius: 50%;
    background: var(--brand-gold);
  }
  .brand__name {
    font-family: "Michroma", sans-serif;
    font-size: 40px; letter-spacing: 3px;
    text-transform: uppercase;
    color: var(--ink);
  }
  .person {
    position: absolute; left: 0; right: 0; top: 290px;
    text-align: center;
  }
  .person__name {
    font-family: "Michroma", sans-serif;
    font-size: 24px; letter-spacing: 2px;
    color: var(--muted);
  }
  .person__role {
    margin-top: 10px;
    font-family: "Exo 2", sans-serif;
    font-size: 22px; letter-spacing: 1px;
    color: var(--brand-gold);
  }

  /* Back */
  .back-art { position: absolute; inset: 0; }
  .contact {
    position: absolute; top: 290px; width: 280px;
    text-align: center;
    font-family: "Exo 2", sans-serif;
    font-size: 22px; line-height: 1.4; letter-spacing: 1px;
    color: var(--white);
  }
  .contact--phone { left: 50px; }
  .contact--address { left: 280px; }
  .contact--web { left: 510px; }
</style>
</head>
<body>

<section class="card card--front">
  <div class="brand">
    <span class="brand__mark"></span>
    <span class="brand__name">Marlo clean</span>
  </div>
  <div class="person">
    <p class="person__name">DANA WHITFIELD</p>
    <p class="person__role">Managing Director</p>
  </div>
</section>

<section class="card card--back">
  <svg class="back-art" width="840" height="480" viewBox="0 0 840 480">
    <path fill="var(--brand-teal)" d="M0,480 V240
      C60,240 90,242 110,240
      C130,240 135,150 190,150 C245,150 250,240 270,240
      C300,240 320,242 340,240
      C360,240 365,150 420,150 C475,150 480,240 500,240
      C530,240 550,242 570,240
      C590,240 595,150 650,150 C705,150 710,240 730,240
      C770,240 800,236 840,232 V480 Z"/>
    <g fill="none" stroke="var(--gold-light)" stroke-width="3" stroke-linecap="round" stroke-linejoin="round">
      <circle class="icon-ring" cx="190" cy="200" r="28"/>
      <circle class="icon-ring" cx="420" cy="200" r="28"/>
      <circle class="icon-ring" cx="650" cy="200" r="28"/>
    </g>
    <g fill="none" stroke="var(--white)" stroke-width="3" stroke-linecap="round" stroke-linejoin="round">
      <path class="icon-phone" d="M180,187 c-4,2 -5,6 -3,11 c3,7 8,12 15,15 c5,2 9,1 11,-3 l-5,-5 l-4,3 c-4,-2 -7,-5 -9,-9 l3,-4 z"/>
      <path class="icon-pin" d="M420,216 c-8,-9 -12,-15 -12,-21 a12,12 0 0 1 24,0 c0,6 -4,12 -12,21 z"/>
      <circle class="icon-pin" cx="420" cy="195" r="4"/>
      <g class="icon-globe">
        <circle cx="650" cy="200" r="15"/>
        <ellipse cx="650" cy="200" rx="6" ry="15"/>
        <path d="M635,200 h30 M638,192 h24 M638,208 h24"/>
      </g>
    </g>
  </svg>
  <p class="contact contact--phone">012 555 0148<br>012 555 0148</p>
  <p class="contact contact--address">214, 6th floor,<br>Harbor View Road<br>SD</p>
  <p class="contact contact--web">hello@marloclean.com<br>marloclean.com</p>
</section>

</body>
</html>
```